Business Card for Vorla Parts Wholesale supplier

Hi There! I need a new business card for our company. We are specialized in selling Vorla parts, mostly we sell new LCD screens for Zelnar and Drelks. I would like to see that back in the design.

You can find the colors and logo's on our website: www.hartuvo.nl

Industry/Entity Type

Business

Contact Information for Business Card

My Details:
Tobias Lindqvist

Phone: 0031687203316
E-mail: Tobias@hartuvo.nl

Slogan: "Because Quality Matters"

Font styles to use
Sans Serif

Colors

Designer to choose colors to be used in the design.

Requirements
Must have
• A Black backside with the Hartuvo logo on it. The front side should be clean with only my contact details.
• But I'm also open for something really different or awesome!
Nice to have
• Remember that we are in the parts & repairing industry, So i'll be handing those business cards mainly to repair companies. Maybe you can do something with that thought :)

```html
<!DOCTYPE html>
<html lang="en">
<head>
<meta charset="utf-8">
<title>Hartuvo Business Card</title>
<link href="https://fonts.googleapis.com/css2?family=Exo+2:wght@300;400;600;700&display=swap" rel="stylesheet">
<style>
  :root {
    --orange: #f07622;
    --black: #000000;
    --white: #ffffff;
    --ink: #1a1a1a;
    --grey-text: #555555;
    --divider: #c8c8c8;
    --page: #ececec;
  }
  * { margin: 0; padding: 0; box-sizing: border-box; }
  html, body {
    width: 1200px; height: 987px; overflow: hidden;
    background: var(--page);
    font-family: "Exo 2", sans-serif;
  }
  .canvas { position: relative; width: 1200px; height: 987px; }
  .card {
    position: absolute; width: 615px; height: 352px;
    box-shadow: 0 2px 6px rgba(0,0,0,0.25);
  }
  .card--front { left: 293px; top: 130px; background: var(--white); }
  .card--back { left: 292px; top: 505px; background: var(--black); }
  .card__frame { position: absolute; inset: 0; }

  .brand { position: absolute; display: flex; align-items: center; }
  .brand__dot { border-radius: 50%; background: var(--orange); flex: none; }
  .brand__name { font-weight: 600; line-height: 1; letter-spacing: 0.5px; }

  .card--front .brand { left: 80px; top: 151px; gap: 12px; }
  .card--front .brand__dot { width: 46px; height: 46px; }
  .card--front .brand__name { font-size: 44px; color: var(--ink); }

  .divider {
    position: absolute; left: 335px; top: 110px;
    width: 1px; height: 127px; background: var(--divider);
  }
  .contact { position: absolute; left: 363px; top: 114px; }
  .contact__name {
    font-size: 24px; font-weight: 600; color: var(--orange);
    letter-spacing: 0.6px; margin-bottom: 14px;
  }
  .contact__row {
    display: flex; align-items: center; gap: 7px;
    font-size: 16px; font-weight: 400; color: var(--grey-text);
    height: 23.5px; padding-left: 2px;
  }
  .contact__icon { width: 15px; height: 15px; flex: none; }

  .card--back .brand { left: 128px; top: 130px; gap: 18px; }
  .card--back .brand__dot { width: 70px; height: 70px; }
  .card--back .brand__name { font-size: 64px; color: var(--white); }
  .tagline {
    position: absolute; left: 0; right: 0; top: 266px;
    text-align: center; font-size: 21px; font-weight: 700;
    color: var(--orange); letter-spacing: 0.4px;
  }
</style>
</head>
<body>
<main class="canvas">

  <section class="card card--front" aria-label="Card front">
    <svg class="card__frame" width="615" height="352" viewBox="0 0 615 352">
      <polygon points="31,14 584,14 601,31 601,321 584,338 31,338 14,321 14,31"
               fill="none" stroke="#f07622" stroke-width="2"/>
    </svg>
    <div class="brand">
      <span class="brand__dot"></span>
      <span class="brand__name">hartuvo</span>
    </div>
    <div class="divider"></div>
    <div class="contact">
      <div class="contact__name">Tobias Lindqvist</div>
      <div class="contact__row">
        <svg class="contact__icon" viewBox="0 0 16 16" aria-hidden="true">
          <path fill="#f07622" d="M3.6 1.2l2.3 2.8-1.4 1.8c.8 2 2.3 3.6 4.3 4.5l1.8-1.4 2.8 2.3-1.2 2.3c-5.6-.6-10-5-10.6-10.6z"/>
        </svg>
        <span>0031687203316</span>
      </div>
      <div class="contact__row">
        <svg class="contact__icon" viewBox="0 0 16 16" aria-hidden="true">
          <rect x="1.5" y="3.5" width="13" height="9" fill="#f07622"/>
          <path d="M1.5 3.8L8 9l6.5-5.2" fill="none" stroke="#fff" stroke-width="1.2"/>
        </svg>
        <span>Tobias@hartuvo.nl</span>
      </div>
      <div class="contact__row">
        <svg class="contact__icon" viewBox="0 0 16 16" aria-hidden="true">
          <circle cx="8" cy="8" r="6.8" fill="#f07622"/>
          <path d="M1.5 8h13M8 1.2c-2.4 2-2.4 11.6 0 13.6M8 1.2c2.4 2 2.4 11.6 0 13.6" fill="none" stroke="#fff" stroke-width="1"/>
        </svg>
        <span>www.hartuvo.nl</span>
      </div>
    </div>
  </section>

  <section class="card card--back" aria-label="Card back">
    <svg class="card__frame" width="615" height="352" viewBox="0 0 615 352">
      <polygon points="31,14 584,14 601,31 601,321 584,338 31,338 14,321 14,31"
               fill="none" stroke="#f07622" stroke-width="2"/>
    </svg>
    <div class="brand">
      <span class="brand__dot"></span>
      <span class="brand__name">hartuvo</span>
    </div>
    <p class="tagline">Because Quality Matters</p>
  </section>

</main>
</body>
</html>
```